Marketing - Outdoor Vinyl banner, Outdoor Poster, Flyer modifications

Hi, I worked with you in the past and attached flyer designs. It just needs to be tweaked for various prints.
1)Outdoor vinyl banner (4 feet height and 8 feet width) print: Just grand opening pic, logo with name, tagline and call/text us portion.
2)Outdoor Poster (5 feet height and 3 feet width) print: same as above
3) Indoor poster for both horizontal & Vertical prints: Just logo w/ name, tagline, "We are MOVING Next door"
4)Flyer: will give minor modifications to attached flyer designs

```html
<!DOCTYPE html>
<html lang="en">
<head>
<meta charset="UTF-8">
<title>Brightway Dental – Moving Next Door</title>
<link href="https://fonts.googleapis.com/css2?family=Roboto+Slab:wght@700;800&display=swap" rel="stylesheet">
<style>
  :root {
    --navy: #00355c;
    --cyan: #0bb1d9;
    --white: #ffffff;
    --backdrop: #e6e8eb;
  }
  * { margin: 0; padding: 0; box-sizing: border-box; }
  html, body {
    width: 1096px;
    height: 1200px;
    overflow: hidden;
    background: var(--backdrop);
  }
  .poster {
    position: absolute;
    left: 179px;
    top: 30px;
    width: 738px;
    height: 1140px;
    display: flex;
    flex-direction: column;
    font-family: "Roboto Slab", Georgia, serif;
    font-weight: 700;
  }
  .poster__header {
    height: 267px;
    background: var(--navy);
    display: flex;
    align-items: center;
    justify-content: center;
    gap: 18px;
  }
  .brand__dot {
    width: 58px;
    height: 58px;
    border-radius: 50%;
    background: var(--cyan);
  }
  .brand__name {
    color: var(--cyan);
    font-size: 52px;
    letter-spacing: 1px;
  }
  .poster__body {
    height: 684px;
    background: var(--cyan);
    color: var(--white);
    text-align: center;
    position: relative;
  }
  .announcement__lead {
    position: absolute;
    top: 122px;
    width: 100%;
    font-size: 54px;
    line-height: 1;
  }
  .announcement__headline {
    position: absolute;
    top: 266px;
    width: 100%;
    font-size: 146px;
    line-height: 139px;
    font-weight: 800;
    letter-spacing: 1px;
  }
  .poster__footer {
    height: 189px;
    background: var(--navy);
    display: flex;
    align-items: center;
    justify-content: center;
  }
  .tagline {
    color: var(--cyan);
    font-size: 52px;
    line-height: 1;
  }
</style>
</head>
<body>
  <main class="poster">
    <header class="poster__header">
      <span class="brand__dot" aria-hidden="true"></span>
      <span class="brand__name">Brightway Dental</span>
    </header>
    <section class="poster__body">
      <p class="announcement__lead">We are MOVING</p>
      <h1 class="announcement__headline">NEXT<br>DOOR!</h1>
    </section>
    <footer class="poster__footer">
      <p class="tagline">Excited to find home!</p>
    </footer>
  </main>
</body>
</html>
```